use my brand and make an elegant business card  with it

Target Market(s)
male and female ' ages 25 to 45 age- who appreciate the highest quality goods, experiences, services, brands and relationships
Industry/Entity Type
Business
Requirements
Must have
- my logo integrated into the design-note the uploaded file
front: just logo and the phrase: New. Trend. Life. Style
back informations:
Maren Tosvik
Director
phone: +1 604 2957318
www.matosvik.com
email: marentosvik@matosvik.com
the pin of Facebook (F) and tweeter (T)
Nice to have
- contrast of the colors black gold and silver
Should not have
- cartoons or whimsical design

```html
<!DOCTYPE html>
<html lang="en">
<head>
<meta charset="utf-8">
<title>Maren Tosvik — Business Card</title>
<link rel="stylesheet" href="https://fonts.googleapis.com/css2?family=Cinzel:wght@400;500&family=Old+Standard+TT:wght@400&family=Quicksand:wght@700&display=swap">
<style>
  :root {
    --card-black: #0c0c0c;
    --card-black-soft: #1a1a1a;
    --gold: #c8900a;
    --silver: #b9b9b9;
    --grey: #8e8e8e;
    --grey-dark: #6f6f6f;
    --crest-tone: #1e2628;
  }
  html, body {
    margin: 0;
    padding: 0;
    width: 1200px;
    height: 720px;
    overflow: hidden;
    background: var(--card-black);
  }
  .card {
    position: relative;
    width: 1200px;
    height: 720px;
    overflow: hidden;
    background: radial-gradient(ellipse at 40% 35%, var(--card-black-soft) 0%, var(--card-black) 75%);
  }
  .crest-decoration {
    position: absolute;
    left: 923px;
    top: 64px;
    width: 277px;
    height: 597px;
    border-radius: 140px 40px 20px 120px;
    background: linear-gradient(160deg, var(--crest-tone) 0%, rgba(30, 38, 40, 0.75) 60%, rgba(30, 38, 40, 0.2) 100%);
  }
  .tagline {
    position: absolute;
    top: 66px;
    left: 0;
    width: 1216px;
    margin: 0;
    text-align: center;
    font-family: "Cinzel", serif;
    font-weight: 500;
    font-size: 33px;
    letter-spacing: 3px;
    color: var(--silver);
  }
  .divider {
    position: absolute;
    left: 596px;
    top: 109px;
    width: 7px;
    height: 517px;
    background: var(--gold);
  }
  .identity {
    position: absolute;
    left: 139px;
    top: 265px;
    width: 400px;
    text-align: center;
  }
  .identity__name {
    margin: 0;
    font-family: "Old Standard TT", serif;
    font-weight: 400;
    font-size: 56px;
    line-height: 1;
    color: var(--gold);
  }
  .identity__role {
    margin: 30px 0 0;
    font-family: "Quicksand", sans-serif;
    font-weight: 700;
    font-size: 36px;
    letter-spacing: 1px;
    color: var(--grey-dark);
  }
  .contact {
    position: absolute;
    left: 648px;
    display: flex;
    align-items: center;
    margin: 0;
    color: var(--grey);
    font-family: "Old Standard TT", serif;
    text-decoration: none;
  }
  .contact__icon {
    width: 50px;
    height: 50px;
    flex: none;
    margin-right: 26px;
  }
  .contact--phone {
    top: 305px;
    font-size: 48px;
    letter-spacing: 3px;
  }
  .contact--email {
    top: 372px;
    font-size: 25px;
    letter-spacing: 0.6px;
    text-transform: uppercase;
  }
  .corner-mark {
    position: absolute;
    left: 39px;
    top: 599px;
    width: 60px;
    height: 82px;
  }
  .website {
    position: absolute;
    left: 107px;
    top: 646px;
    margin: 0;
    font-family: "Old Standard TT", serif;
    font-size: 34px;
    line-height: 1;
    text-transform: uppercase;
    color: var(--grey-dark);
  }
  .website__name { color: var(--gold); }
  .social {
    position: absolute;
    left: 677px;
    top: 619px;
    display: flex;
    gap: 12px;
  }
  .social__pin {
    width: 40px;
    height: 40px;
    border-radius: 50%;
    background: var(--gold);
  }
  .brand-name {
    position: absolute;
    left: 802px;
    top: 612px;
    margin: 0;
    font-family: "Old Standard TT", serif;
    font-weight: 400;
    font-size: 50px;
    line-height: 1;
    color: var(--gold);
    white-space: nowrap;
  }
</style>
</head>
<body>
  <main class="card">
    <div class="crest-decoration" role="img" aria-label="Large faint brand crest decoration"></div>

    <p class="tagline">New. Trend. Life. Style</p>

    <div class="divider"></div>

    <section class="identity">
      <h1 class="identity__name">Maren Tosvik</h1>
      <p class="identity__role">DIRECTOR</p>
    </section>

    <p class="contact contact--phone">
      <svg class="contact__icon" viewBox="0 0 50 50" aria-hidden="true">
        <circle cx="25" cy="25" r="22" fill="none" stroke="var(--gold)" stroke-width="3"/>
        <path d="M17 13c2-1 3 0 4 2l2 4c1 2 0 3-1 4l-1 1c1 3 4 6 7 7l1-1c1-1 2-2 4-1l4 2c2 1 3 2 2 4l-1 2c-1 2-4 3-7 2-8-3-13-8-16-16-1-3 0-6 2-7z" fill="var(--gold)"/>
      </svg>
      +1 604 2957318
    </p>

    <p class="contact contact--email">
      <svg class="contact__icon" viewBox="0 0 50 50" aria-hidden="true">
        <circle cx="25" cy="25" r="22" fill="none" stroke="var(--gold)" stroke-width="3"/>
        <rect x="12" y="16" width="26" height="18" fill="var(--gold)"/>
        <path d="M12 16l13 11 13-11" fill="none" stroke="var(--card-black)" stroke-width="2"/>
      </svg>
      marentosvik@matosvik.com
    </p>

    <svg class="corner-mark" viewBox="0 0 60 82" aria-hidden="true">
      <defs>
        <linearGradient id="corner-fill" x1="0" y1="0" x2="1" y2="1">
          <stop offset="0" stop-color="#9a9a9a"/>
          <stop offset="1" stop-color="#5e5e5e"/>
        </linearGradient>
      </defs>
      <polygon points="0,0 60,82 0,82" fill="url(#corner-fill)"/>
    </svg>

    <p class="website">www.<span class="website__name">matosvik</span>.com</p>

    <div class="social" role="img" aria-label="Social network profile pins">
      <span class="social__pin"></span>
      <span class="social__pin"></span>
    </div>

    <p class="brand-name">Ma Tosvik</p>
  </main>
</body>
</html>
```